DESKHAVEN COSPACE Website design and coding

DESKHAVEN COSPACE

DESKHAVEN is Galveston’s first (and currently only) shared business co-working space. We share the same upscale, casual work environment, but we work independently on our own (or our team’s) projects and goals. For only a flat $195 membership fee per month, you have your very own all-inclusive, fun, personal business office environment. Website is written (Word file #12, below); and all pictures etc provided. Galveston is a beachy, coastal, historic city an hour from Houston, Texas USA. Logo (file 11 below) is temporary only.

Target Market(s)

Outside sales people, medical students looking for study hall, Houston companies looking for local office, real estate agents, graphic artists, entrepreneurs, etc

Contact Information for Business Card

will discuss --want to combine with current business card with multiple businesses

Logo Text

DESKHAVEN COSPACE

Coding

Coded - Design and coding required

Number of Pages Required

5+ page

Colors
ec1f27
fbed22

Requirements
Nice to have
• maroon/wine dominant with yellow and red accents, gray base are the colors of the space--website could coordinate--but open to creative ideas/combinations

```html
<!DOCTYPE html>
<html lang="en">
<head>
<meta charset="utf-8">
<title>DESKHAVEN COSPACE</title>
<link href="https://fonts.googleapis.com/css2?family=Montserrat:wght@400;600;700;800&family=Roboto:wght@300;400;500&display=swap" rel="stylesheet">
<style>
:root{
  --red:#ec1f27;
  --yellow:#fbed22;
  --wine:#6e0010;
  --wine-deep:#3f0008;
  --black:#000;
  --charcoal:#1c1c1c;
  --gray:#2e2e2e;
  --text:#e8e8e8;
  --muted:#b9b9b9;
}
*{box-sizing:border-box;margin:0;padding:0}
html,body{width:1200px;height:5164px;overflow:hidden;background:#000}
body{font-family:'Roboto',sans-serif;color:var(--text);position:relative}
section,header,footer{position:absolute;left:0;width:1200px;overflow:hidden}
.heading{font-family:'Montserrat',sans-serif;font-weight:700;color:#fff;letter-spacing:.5px}
.bar{position:absolute;height:3px;width:64px;background:var(--yellow)}
.btn{position:absolute;font-family:'Montserrat',sans-serif;font-weight:700;font-size:13px;letter-spacing:1px;display:flex;align-items:center;justify-content:center}

/* header */
.site-header{top:0;height:100px;background:#000}
.brand{position:absolute;left:78px;top:16px;font-family:'Montserrat',sans-serif;font-weight:800;color:var(--yellow);font-size:30px;line-height:30px;text-align:center}
.brand small{display:block;font-size:19px;line-height:24px;letter-spacing:1px}
.nav{position:absolute;top:40px;font-family:'Montserrat',sans-serif;font-size:12px;color:#ddd;white-space:nowrap}
.nav.active{color:var(--yellow);font-weight:700}
.phone{position:absolute;left:1016px;top:35px;font-family:'Montserrat',sans-serif;font-weight:700;font-size:16px;color:#fff;display:flex;align-items:center;gap:8px}

/* hero */
.hero{top:100px;height:680px}
.hero-photo{position:absolute;inset:0;background:linear-gradient(180deg,#8a6a45 0%,#5a4a38 35%,#3b3128 65%,#1d1a18 100%)}
.hero-shade{position:absolute;left:0;right:0;bottom:0;height:280px;background:linear-gradient(180deg,rgba(0,0,0,0),rgba(20,20,40,.75))}
.hero h1{position:absolute;left:0;width:1200px;top:550px;text-align:center;font-family:'Montserrat',sans-serif;font-weight:700;font-size:40px;color:#fff}
.hero p{position:absolute;left:0;width:1200px;top:612px;text-align:center;font-size:14px;line-height:20px;color:#eee}
.arrow{position:absolute;top:260px;width:34px;height:60px;background:rgba(40,40,40,.85);display:flex;align-items:center;justify-content:center}

/* about */
.about{top:780px;height:612px;background:linear-gradient(160deg,#050505 0%,#2a2a2a 100%)}
.diamond-frame{position:absolute;left:104px;top:44px;width:500px;height:500px}
.about h2{position:absolute;left:644px;top:122px;font-size:32px;line-height:40px}
.about p{position:absolute;left:644px;top:244px;width:444px;font-size:13.5px;line-height:26px;color:var(--muted)}

/* amenities */
.amenities{top:1392px;height:800px;background:linear-gradient(150deg,#8a0013 0%,#5c000c 55%,#3a0008 100%)}
.amenities h2{position:absolute;left:0;width:1200px;top:70px;text-align:center;font-size:32px}
.amenities .lead{position:absolute;left:0;width:1200px;top:134px;text-align:center;font-size:16px;line-height:28px;color:#fff}
.amenity{position:absolute;width:240px;display:flex;align-items:center;gap:12px;font-size:12.5px;line-height:18px;color:#fff}
.amenity svg{flex:0 0 44px}

/* gallery */
.gallery{top:2192px;height:700px;background:linear-gradient(180deg,#1a1a1a,#2b2b2b)}
.gallery h2{position:absolute;left:0;width:1200px;top:62px;text-align:center;font-size:32px}
.shot{position:absolute}

/* philosophy */
.philosophy{top:2892px;height:812px;background:#000}
.philosophy h2{position:absolute;left:0;width:1200px;top:74px;text-align:center;font-size:32px}
.card{position:absolute;width:434px;height:258px;border:2px solid var(--red);text-align:center}
.card.gold{border-color:#cfc21c}
.card h3{position:absolute;left:0;right:0;top:94px;font-family:'Montserrat',sans-serif;font-weight:600;font-size:15px;color:#fff}
.card p{position:absolute;left:30px;right:30px;top:124px;font-size:11.5px;line-height:19px;color:var(--muted)}
.card svg{position:absolute;left:192px;top:26px}

/* membership */
.membership{top:3704px;height:552px;background:#000}
.membership-photo{position:absolute;left:0;top:0;width:620px;height:552px;background:linear-gradient(160deg,#6e7a86 0%,#8a6b3d 45%,#c79a55 75%,#6a5030 100%)}
.membership h2{position:absolute;left:696px;top:92px;font-size:32px}
.price{position:absolute;left:696px;top:178px;font-family:'Montserrat',sans-serif;font-weight:700;font-size:34px;color:#fff}
.price em{font-style:normal;color:var(--red)}
.price sub{font-size:17px;color:var(--red);vertical-align:baseline;font-weight:600}
.membership p{position:absolute;left:696px;width:386px;font-size:13.5px;line-height:26px;color:var(--muted)}
.membership .offer{color:var(--yellow)}
.offer u{text-decoration:underline}

/* contact */
.contact{top:4256px;height:504px;background:linear-gradient(150deg,#9a0016 0%,#70000f 60%,#4e000b 100%)}
.contact h2{position:absolute;left:0;width:1200px;top:74px;text-align:center;font-size:32px}
.field{position:absolute;left:178px;width:436px;height:44px;background:#fff;color:#777;font-size:11.5px;padding:14px 16px}
.field.message{left:626px;width:434px;height:210px}

/* footer */
.site-footer{top:4760px;height:324px;background:#000}
.foot-brand{position:absolute;left:144px;top:72px;font-family:'Montserrat',sans-serif;font-weight:800;font-size:35px;line-height:34px;color:var(--yellow)}
.foot-brand small{display:block;font-size:23px;line-height:28px;letter-spacing:1px}
.foot-desc{position:absolute;left:144px;top:150px;width:216px;font-size:10.5px;line-height:19px;color:var(--muted)}
.foot-title{position:absolute;top:70px;font-family:'Montserrat',sans-serif;font-weight:700;font-size:13px;color:#fff;letter-spacing:.5px}
.foot-link{position:absolute;display:flex;align-items:center;gap:10px;font-size:11.5px;color:#ccc;white-space:nowrap}
.tick{width:13px;height:13px;border:1px solid #777;border-radius:50%}
.dot{width:22px;height:22px;border-radius:50%;background:var(--yellow)}
.copyright{position:absolute;left:0;top:5084px;width:1200px;height:80px;background:#0b0b0b;text-align:center;font-size:10px;color:#999;padding-top:34px}
</style>
</head>
<body>

<header class="site-header">
  <div class="brand">DESKHAVEN<small>COSPACE</small></div>
  <span class="nav active" style="left:304px">ABOUT</span>
  <span class="nav" style="left:386px">AMENITIES</span>
  <span class="nav" style="left:490px">MEMBERSHIP</span>
  <span class="nav" style="left:608px">GALLERY</span>
  <span class="nav" style="left:694px">THE DESKHAVEN PHILOSOPHY</span>
  <span class="nav" style="left:920px">CONTACT</span>
  <div class="phone">
    <svg width="16" height="16" viewBox="0 0 24 24"><path fill="#fbed22" d="M6.6 10.8a15 15 0 0 0 6.6 6.6l2.2-2.2c.3-.3.7-.4 1-.2 1.1.4 2.3.6 3.6.6.6 0 1 .4 1 1V20c0 .6-.4 1-1 1A17 17 0 0 1 3 4c0-.6.4-1 1-1h3.5c.6 0 1 .4 1 1 0 1.3.2 2.5.6 3.6.1.3 0 .7-.2 1z"/></svg>
    713-555-0148
  </div>
</header>

<section class="hero">
  <div class="hero-photo" role="img" aria-label="Photo of the coworking lounge with pendant lamps, desks with yellow and black chairs and a glass-walled office"></div>
  <div class="hero-shade"></div>
  <div class="arrow" style="left:0"><svg width="14" height="26" viewBox="0 0 14 26"><path d="M12 2 2 13l10 11" stroke="#fff" stroke-width="2" fill="none"/></svg></div>
  <div class="arrow" style="left:1166px"><svg width="14" height="26" viewBox="0 0 14 26"><path d="M2 2l10 11L2 24" stroke="#fff" stroke-width="2" fill="none"/></svg></div>
  <h1>WORK OUTSIDE THE HOME</h1>
  <p>Free yourself for the burdens of house or school, and work in an environment that<br>MOTIVATES you instead of DISTRACTS you</p>
</section>

<section class="about">
  <svg class="diamond-frame" viewBox="0 0 500 500">
    <defs><linearGradient id="aboutPhoto" x1="0" y1="0" x2="1" y2="1"><stop offset="0" stop-color="#3a4a66"/><stop offset=".55" stop-color="#5b5f66"/><stop offset="1" stop-color="#d8d4c8"/></linearGradient></defs>
    <polygon points="250,2 498,250 250,498 2,250" fill="none" stroke="#8a8a8a" stroke-width="3"/>
    <polygon points="250,18 482,250 250,482 18,250" fill="url(#aboutPhoto)" role="img" aria-label="Photo of the lounge with black leather sofas, lockers and a white couch"/>
  </svg>
  <h2 class="heading">ABOUT<br>DESKHAVEN COSPACE</h2>
  <div class="bar" style="left:644px;top:212px"></div>
  <p>DESKHAVEN is Galveston's first (and currently only) shared business co-working space. We share the same upscale, casual work environment, but we work independently on our own (or our team's) projects and goals. For only a flat $195 membership fee per month, you have your very own all-inclusive, fun, personal business office environment.</p>
  <div class="btn" style="left:648px;top:432px;width:154px;height:38px;background:var(--red);color:#fff">LEARN MORE</div>
</section>

<section class="amenities">
  <h2 class="heading">AMENITIES</h2>
  <div class="bar" style="left:568px;top:116px"></div>
  <p class="lead">DESKHAVEN is the first Galveston co-working space, and offers all of the following features,<br>all included in your monthly $195 membership fee:</p>

  <div class="amenity" style="left:124px;top:246px"><svg width="44" height="40" viewBox="0 0 44 40"><rect x="4" y="8" width="36" height="24" fill="none" stroke="#fbed22" stroke-width="2"/><path d="M10 32v6M34 32v6M4 16h36" stroke="#fbed22" stroke-width="2"/></svg><span>Open office or a<br>private cubicle for<br>your daily use.</span></div>
  <div class="amenity" style="left:372px;top:246px"><svg width="44" height="40" viewBox="0 0 44 40"><path d="M6 16a23 23 0 0 1 32 0M11 22a15 15 0 0 1 22 0M16 28a7 7 0 0 1 12 0" stroke="#fbed22" stroke-width="2.5" fill="none"/><circle cx="22" cy="33" r="2.5" fill="#fbed22"/></svg><span>Free Wifi</span></div>
  <div class="amenity" style="left:624px;top:246px"><svg width="44" height="40" viewBox="0 0 44 40"><rect x="6" y="10" width="32" height="22" fill="none" stroke="#fbed22" stroke-width="2"/><path d="M6 10l16 13 16-13" stroke="#fbed22" stroke-width="2" fill="none"/></svg><span>Mail service</span></div>
  <div class="amenity" style="left:896px;top:246px"><svg width="44" height="40" viewBox="0 0 44 40"><circle cx="22" cy="10" r="5" fill="none" stroke="#fbed22" stroke-width="2"/><path d="M8 34l6-14h16l6 14z" fill="none" stroke="#fbed22" stroke-width="2"/></svg><span>Private conference<br>rooms</span></div>

  <div class="amenity" style="left:124px;top:326px"><svg width="44" height="40" viewBox="0 0 44 40"><rect x="4" y="16" width="36" height="16" fill="none" stroke="#fbed22" stroke-width="2"/><rect x="10" y="8" width="10" height="8" fill="none" stroke="#fbed22" stroke-width="2"/></svg><span>Communal coffee<br>bar and kitchen,<br>with FREE coffee</span></div>
  <div class="amenity" style="left:372px;top:326px"><svg width="44" height="40" viewBox="0 0 44 40"><circle cx="14" cy="12" r="5" fill="none" stroke="#fbed22" stroke-width="2"/><circle cx="30" cy="12" r="5" fill="none" stroke="#fbed22" stroke-width="2"/><path d="M4 34a10 10 0 0 1 20 0M20 34a10 10 0 0 1 20 0" fill="none" stroke="#fbed22" stroke-width="2"/></svg><span>Great opportunity<br>for networking or<br>mentoring</span></div>
  <div class="amenity" style="left:624px;top:326px"><svg width="44" height="40" viewBox="0 0 44 40"><path d="M10 36V10l12-6 12 6v26z" fill="none" stroke="#fbed22" stroke-width="2"/><path d="M16 16h12M16 22h12M16 28h12" stroke="#fbed22" stroke-width="2"/></svg><span>Building is a fabulous<br>example of Mid-Century</span></div>
  <div class="amenity" style="left:896px;top:326px"><svg width="44" height="40" viewBox="0 0 44 40"><circle cx="22" cy="10" r="6" fill="none" stroke="#fbed22" stroke-width="2"/><circle cx="11" cy="28" r="6" fill="none" stroke="#fbed22" stroke-width="2"/><circle cx="33" cy="28" r="6" fill="none" stroke="#fbed22" stroke-width="2"/></svg><span>Great opportunity<br>for networking or<br>mentoring</span></div>

  <div class="amenity" style="left:124px;top:422px"><svg width="44" height="40" viewBox="0 0 44 40"><circle cx="20" cy="20" r="15" fill="none" stroke="#fbed22" stroke-width="2"/><path d="M20 10v10l7 5" stroke="#fbed22" stroke-width="2" fill="none"/></svg><span>24 hour access</span></div>
  <div class="amenity" style="left:372px;top:422px"><svg width="44" height="40" viewBox="0 0 44 40"><path d="M6 22h32M10 22v14M34 22v14M12 6v16h10" stroke="#fbed22" stroke-width="2" fill="none"/></svg><span>Comfortable open<br>casual spaces</span></div>
  <div class="amenity" style="left:624px;top:422px"><svg width="44" height="40" viewBox="0 0 44 40"><rect x="6" y="6" width="32" height="28" fill="none" stroke="#fbed22" stroke-width="2"/><path d="M16 14h12v10a6 6 0 0 1-12 0z" fill="none" stroke="#fbed22" stroke-width="2"/></svg><span>Weekly FREE<br>happy hour</span></div>
  <div class="amenity" style="left:896px;top:422px"><svg width="44" height="40" viewBox="0 0 44 40"><rect x="6" y="6" width="32" height="22" fill="none" stroke="#fbed22" stroke-width="2"/><path d="M22 28v8M14 36h16" stroke="#fbed22" stroke-width="2"/></svg><span>Free conference/<br>presentation room</span></div>

  <div class="amenity" style="left:124px;top:500px"><svg width="44" height="40" viewBox="0 0 44 40"><circle cx="12" cy="10" r="4" fill="none" stroke="#fbed22" stroke-width="2"/><circle cx="32" cy="10" r="4" fill="none" stroke="#fbed22" stroke-width="2"/><path d="M12 16v18M32 16v18M18 22h8" stroke="#fbed22" stroke-width="2"/></svg><span>Health and social<br>distance amenities</span></div>
  <div class="amenity" style="left:372px;top:500px"><svg width="44" height="40" viewBox="0 0 44 40"><rect x="12" y="4" width="20" height="10" fill="none" stroke="#fbed22" stroke-width="2"/><rect x="6" y="14" width="32" height="14" fill="none" stroke="#fbed22" stroke-width="2"/><rect x="12" y="24" width="20" height="12" fill="none" stroke="#fbed22" stroke-width="2"/></svg><span>Use of copier/<br>printer</span></div>
  <div class="amenity" style="left:624px;top:500px"><svg width="44" height="40" viewBox="0 0 44 40"><rect x="8" y="4" width="28" height="32" fill="none" stroke="#fbed22" stroke-width="2"/><path d="M22 4v32M8 14h28M8 24h28" stroke="#fbed22" stroke-width="2"/></svg><span>Private lockable<br>lockers</span></div>
  <div class="amenity" style="left:896px;top:500px"><svg width="44" height="40" viewBox="0 0 44 40"><path d="M14 4h16v14a8 8 0 0 1-16 0zM22 26v10M14 36h16" fill="none" stroke="#fbed22" stroke-width="2"/></svg><span>Very comfortable<br>private office chairs</span></div>

  <div class="amenity" style="left:124px;top:580px"><svg width="44" height="40" viewBox="0 0 44 40"><rect x="6" y="4" width="28" height="32" fill="none" stroke="#fbed22" stroke-width="2"/><path d="M12 28l6-8 5 5 7-10" stroke="#fbed22" stroke-width="2" fill="none"/></svg><span>Great modern design<br>a place that looks</span></div>
  <div class="amenity" style="left:372px;top:580px"><svg width="44" height="40" viewBox="0 0 44 40"><rect x="10" y="4" width="24" height="32" rx="2" fill="none" stroke="#fbed22" stroke-width="2"/><path d="M16 12h12M16 18h4M24 18h4M16 24h4M24 24h4" stroke="#fbed22" stroke-width="2"/></svg><span>Keyless, digital<br>door entry</span></div>
  <div class="amenity" style="left:624px;top:580px"><svg width="44" height="40" viewBox="0 0 44 40"><path d="M12 4v10a4 4 0 0 0 8 0V4M16 4v32M28 4c6 4 6 14 0 16v16" stroke="#fbed22" stroke-width="2" fill="none"/></svg><span>Kitchen and<br>bar area</span></div>
  <div class="amenity" style="left:896px;top:580px"><svg width="44" height="40" viewBox="0 0 44 40"><rect x="6" y="4" width="32" height="32" rx="6" fill="none" stroke="#fbed22" stroke-width="2"/><circle cx="20" cy="20" r="7" fill="none" stroke="#fbed22" stroke-width="2"/></svg><span>Nightly ozone<br>hospital grade</span></div>

  <div class="btn" style="left:526px;top:690px;width:154px;height:40px;background:var(--yellow);color:#000">LEARN MORE</div>
</section>

<section class="gallery">
  <h2 class="heading">OUR GALLERY</h2>
  <div class="bar" style="left:568px;top:108px"></div>
  <div class="shot" style="left:126px;top:144px;width:474px;height:224px;background:linear-gradient(180deg,#6b6e74,#3c3c40 60%,#c99a48)" role="img" aria-label="Photo of the lounge with lockers, white sofa and a wooden table"></div>
  <div class="shot" style="left:610px;top:144px;width:476px;height:224px;background:linear-gradient(90deg,#3a3a36,#d6c66a 25%,#4a4a4a 55%,#888 75%,#2f2f2f)" role="img" aria-label="Photo of yellow and black office chairs and a hallway"></div>
  <div class="shot" style="left:126px;top:384px;width:312px;height:208px;background:linear-gradient(180deg,#9aa2a6,#c79b52 70%,#6a4f2c)" role="img" aria-label="Photo of wooden desks under pendant lamps"></div>
  <div class="shot" style="left:450px;top:384px;width:312px;height:208px;background:linear-gradient(180deg,#6f6a62,#a89c82 50%,#3d3a35)" role="img" aria-label="Photo of a glass office door and a plant"></div>
  <div class="shot" style="left:774px;top:384px;width:312px;height:208px;background:linear-gradient(180deg,#5a5a5a,#8a8780 50%,#2e2e2e)" role="img" aria-label="Photo of the kitchen with stainless appliances and bar stools"></div>
</section>

<section class="philosophy">
  <h2 class="heading">THE DESKHAVEN PHILOSOPHY</h2>
  <div class="bar" style="left:568px;top:120px"></div>

  <div class="card" style="left:156px;top:152px">
    <svg width="50" height="50" viewBox="0 0 50 50"><path d="M6 24h38M10 24v22M40 24v22M18 24v-8h14v8M20 34h10" stroke="#ec1f27" stroke-width="2.5" fill="none"/><circle cx="25" cy="8" r="4" fill="none" stroke="#ec1f27" stroke-width="2.5"/></svg>
    <h3>WORK OUTSIDE THE HOME</h3>
    <p>Free yourself for the burdens of house or school, and work in an environment that MOTIVATES you instead of DISTRACTS you. Meet like-minded people that can help you along, and yet you have the option to work in a quiet and very comfortable – private office cubicle.</p>
  </div>
  <div class="card gold" style="left:606px;top:152px">
    <svg width="50" height="50" viewBox="0 0 50 50"><circle cx="14" cy="12" r="4" fill="none" stroke="#fbed22" stroke-width="2.5"/><circle cx="36" cy="12" r="4" fill="none" stroke="#fbed22" stroke-width="2.5"/><path d="M6 28h38M14 18v10M36 18v10M12 28v16M38 28v16M25 28v16" stroke="#fbed22" stroke-width="2.5" fill="none"/></svg>
    <h3>WORK IT OUT WITH YOUR COWORKERS</h3>
    <p>DESKHAVEN is a community – if you are making a pot of (free) coffee – ask and make enough for everyone that wants some! You rapidly become part of more than an office – you have new friends, teachers, people you can trade skills and your experience with!</p>
  </div>
  <div class="card gold" style="left:156px;top:430px">
    <svg width="50" height="50" viewBox="0 0 50 50"><path d="M17 6h16v12a8 8 0 0 1-16 0zM25 26v10M15 36h20v8H15z" stroke="#fbed22" stroke-width="2.5" fill="none"/></svg>
    <h3>OUTSHINE THE COMPETITION</h3>
    <p>Because of the flexibility, prestigious location, opportunities to meet and network with active professionals, and the available tech and amenities, you have all the tools you need to excel in your chosen field.</p>
  </div>
  <div class="card" style="left:606px;top:430px">
    <svg width="50" height="50" viewBox="0 0 50 50"><circle cx="12" cy="12" r="5" fill="none" stroke="#ec1f27" stroke-width="2.5"/><circle cx="38" cy="40" r="5" fill="none" stroke="#ec1f27" stroke-width="2.5"/><path d="M17 12h18a7 7 0 0 1 0 14H15a7 7 0 0 0 0 14h18" stroke="#ec1f27" stroke-width="2.5" fill="none"/></svg>
    <h3>WORK OUT THE PATH TO YOUR SUCCESS</h3>
    <p>As your business grows, there are other beautiful, "dedicated desk" private executive offices, and full office suites available in the building. Meet your coworkers and synergize with their energy and experience to jump-start your own career.</p>
  </div>
</section>

<section class="membership">
  <div class="membership-photo" role="img" aria-label="Photo of long wooden desks with yellow posts beneath black pendant lamps"></div>
  <h2 class="heading">MEMBERSHIP</h2>
  <div class="bar" style="left:696px;top:144px"></div>
  <div class="price">For only <em>$195</em> <sub>/monthly</sub></div>
  <p style="top:240px">Charged to your credit card, you get the all-inclusive amenities listed above, for one flat fee. The only "extras" are for copies, on a per-copy basis.</p>
  <p style="top:330px">WiFi, coffee, use of the conference room, office use, use of the kitchen and all the other features listed under "AMENITIES" above, are INCLUDED at no additional cost</p>
  <p class="offer" style="top:424px">Get a FREE day, to try us out by emailing us at the <u>link here</u></p>
</section>

<section class="contact">
  <h2 class="heading">CONTACT US</h2>
  <div class="bar" style="left:568px;top:120px"></div>
  <div class="field" style="top:154px">Name</div>
  <div class="field" style="top:208px">Email address</div>
  <div class="field" style="top:264px">Phone Number</div>
  <div class="field" style="top:320px">Description of your Business</div>
  <div class="field message" style="top:154px">Write Message</div>
  <div class="btn" style="left:524px;top:384px;width:182px;height:46px;background:var(--yellow);color:#000">SEND MESSAGE</div>
</section>

<footer class="site-footer">
  <div class="foot-brand">DESKHAVEN<small>COSPACE</small></div>
  <p class="foot-desc">DESKHAVEN is Galveston's first (and currently only) shared business co-working space. We share the same upscale, casual work environment, but we work independently on our own (or our</p>

  <div class="foot-title" style="left:434px">QUICK MENU</div>
  <div class="foot-link" style="left:434px;top:110px"><span class="tick"></span>About</div>
  <div class="foot-link" style="left:434px;top:137px"><span class="tick"></span>Amenities</div>
  <div class="foot-link" style="left:434px;top:164px"><span class="tick"></span>Membership</div>
  <div class="foot-link" style="left:434px;top:191px"><span class="tick"></span>Gallery</div>
  <div class="foot-link" style="left:434px;top:218px"><span class="tick"></span>The Deskhaven Philosophy</div>
  <div class="foot-link" style="left:434px;top:245px"><span class="tick"></span>Contact</div>

  <div class="foot-title" style="left:636px">FOLLOW US</div>
  <div class="foot-link" style="left:636px;top:106px"><span class="dot"></span>Friendboard</div>
  <div class="foot-link" style="left:636px;top:150px"><span class="dot"></span>ProCircle</div>
  <div class="foot-link" style="left:636px;top:194px"><span class="dot"></span>Snapfeed</div>

  <div class="foot-title" style="left:828px">GET IN TOUCH</div>
  <div class="foot-link" style="left:828px;top:106px"><svg width="22" height="22" viewBox="0 0 24 24"><path fill="#fbed22" d="M12 2a7 7 0 0 0-7 7c0 5 7 13 7 13s7-8 7-13a7 7 0 0 0-7-7zm0 9.5A2.5 2.5 0 1 1 12 6a2.5 2.5 0 0 1 0 5.5z"/></svg>418 Harbor Ave, Suite 210 Galveston, TX 77550</div>
  <div class="foot-link" style="left:828px;top:150px"><svg width="22" height="22" viewBox="0 0 24 24"><circle cx="12" cy="12" r="11" fill="#fbed22"/><path fill="#000" d="M8.6 10.6a8 8 0 0 0 4.8 4.8l1.4-1.4c.2-.2.4-.2.6-.1.6.2 1.3.3 2 .3.3 0 .6.3.6.6V17c0 .3-.3.6-.6.6A11.4 11.4 0 0 1 6 7.4c0-.3.3-.6.6-.6H8.8c.3 0 .6.3.6.6 0 .7.1 1.4.3 2 .1.2 0 .4-.1.6z"/></svg>713-555-0148</div>
  <div class="foot-link" style="left:828px;top:194px"><svg width="22" height="22" viewBox="0 0 24 24"><circle cx="12" cy="12" r="11" fill="#fbed22"/><rect x="6" y="8" width="12" height="8" fill="none" stroke="#000" stroke-width="1.5"/><path d="M6 8l6 5 6-5" fill="none" stroke="#000" stroke-width="1.5"/></svg>hello@deskhavenmail.com</div>
</footer>

<div class="copyright">Copyright © 2020 Deskhaven Cospace &nbsp;|&nbsp; Privacy Policy</div>

</body>
</html>
```